Lumbra Deckworks Company (southern african focus for now) needs a e-commerce website

We need a website design for a playing card company based in Southern Africa/United States. We make locally-sourced playing cards (standard 52 card deck, with customized fronts and backs) for everyone and collaborate with local artists to uplift their talents, while celebrating their nation's culture, heritage, beauty and identity. We would like to see designs that use the colours blue (see flag of Eswatini as starting product), white and some red accents (or your recommendation). The final design should communicate elegance, fun and sustainable prosperity.

Target Market(s)

Everyone loves playing cards. From the solo adventurer to the party host, first time learner or expert, young, middle and old, we need to attract a broad audience that appreciates the finer things and supports sustainable, environmentally contentiousness causes that support the local economy and uplift local talent - thing global, act local.

Number of Pages Required

4 page

Font styles to use
Serif
Sans Serif

Requirements
Must have
• Pages to include Home (Main), About (Our Story), Shop and Contact
Nice to have
• While designs may be static, elements of graceful movement would be desirable. Perhaps functionality of scrolling down on homepage showing playing cards in use, front and back. Quindle and Zorvax store's capture that elegant yet rich look.
Should not have
• Too many products. We focus on 1-2.

```html
<!DOCTYPE html>
<html lang="en">
<head>
<meta charset="utf-8">
<title>Lumbra Deckworks — Playing Cards</title>
<link href="https://fonts.googleapis.com/css2?family=Poppins:wght@400;500;600;700;800&family=Roboto:wght@400;500;700&display=swap" rel="stylesheet">
<style>
:root{
  --red:#b5121b;
  --red-dark:#8e0c13;
  --ink:#1d1d1d;
  --muted:#6a6a6a;
  --paper:#ffffff;
  --soft:#f2f2f2;
  --footer:#f1f1f1;
  --blue:#2a5bb8;
  --gold:#f2c230;
}
*{box-sizing:border-box;margin:0;padding:0}
html,body{width:1200px;height:3444px;overflow:hidden}
body{background:var(--paper);font-family:"Roboto",Arial,sans-serif;color:var(--ink);position:relative}
.abs{position:absolute}

/* header */
.site-header{left:0;top:0;width:1200px;height:88px;background:#fff;box-shadow:0 2px 8px rgba(0,0,0,.06);z-index:2}
.logo{left:112px;top:26px;font-family:"Poppins",sans-serif;font-weight:600;font-size:26px;color:var(--ink)}
.nav{right:118px;top:30px;display:flex;gap:34px;align-items:center;font-family:"Poppins",sans-serif;font-size:15px;font-weight:500}
.nav a{color:var(--ink);text-decoration:none;position:relative}
.nav a.active{color:var(--red)}
.nav a.active::after{content:"";position:absolute;left:0;right:0;bottom:-8px;height:2px;background:var(--red)}
.nav .region{color:var(--red);display:flex;align-items:center;gap:8px}
.region-dot{width:26px;height:26px;border-radius:50%;background:linear-gradient(180deg,var(--blue) 0 28%,var(--gold) 28% 34%,var(--red) 34% 66%,var(--gold) 66% 72%,var(--blue) 72%)}

/* hero */
.hero{left:0;top:88px;width:1200px;height:452px;background:linear-gradient(180deg,#fbfbfb,#f2f2f2)}
.hero-title{left:160px;top:228px;font-family:"Poppins",sans-serif;font-weight:800;font-size:60px;letter-spacing:2px;line-height:72px;color:var(--red)}
.hero-text{left:160px;top:300px;width:440px;font-size:15px;line-height:22px;color:var(--muted)}
.btn{display:inline-block;background:var(--red);color:#fff;font-family:"Poppins",sans-serif;font-weight:600;font-size:13px;letter-spacing:.5px;border-radius:24px;text-align:center;text-decoration:none}
.hero-btn{left:160px;top:368px;width:140px;height:48px;line-height:48px}
.card-back{border-radius:14px;border:6px solid #fff;box-shadow:0 10px 28px rgba(0,0,0,.22);
  background:linear-gradient(180deg,var(--blue) 0 20%,var(--gold) 20% 25%,var(--red) 25% 75%,var(--gold) 75% 80%,var(--blue) 80%)}
.hero-fan{left:700px;top:110px;width:330px;height:300px;border-radius:16px;transform:rotate(-8deg);
  background:linear-gradient(100deg,#fff 0%,#f0f0f0 55%,#e3e3e3 100%);box-shadow:0 8px 24px rgba(0,0,0,.12)}
.hero-card{left:770px;top:180px;width:220px;height:300px}

/* band */
.band{left:0;top:572px;width:1200px;height:68px;background:var(--red);color:#fff;font-family:"Poppins",sans-serif;font-weight:700;font-size:22px;text-align:center;line-height:68px;letter-spacing:.5px}

/* products */
.product{top:704px;width:308px;height:336px;background:var(--soft);box-shadow:0 2px 10px rgba(0,0,0,.08)}
.product-fan{position:absolute;left:66px;top:34px;width:150px;height:150px;border-radius:10px;transform:rotate(-10deg);background:linear-gradient(100deg,#fff,#e2e2e2);box-shadow:0 4px 12px rgba(0,0,0,.12)}
.product-card{position:absolute;left:136px;top:26px;width:112px;height:168px;border-width:4px;border-radius:8px}
.product-name{position:absolute;left:0;right:0;top:244px;text-align:center;font-family:"Poppins",sans-serif;font-weight:700;font-size:22px}
.product-rule{position:absolute;left:134px;top:290px;width:40px;height:3px;background:var(--red)}
.arrow{top:856px}

/* story */
.story-photo{left:0;top:1148px;width:600px;height:404px;
  background:linear-gradient(180deg,#2f4a22 0%,#4f6a33 28%,#9b8a72 50%,#c9c3b8 62%,#7f969a 80%,#5d7478 100%)}
.play{left:262px;top:1314px;width:72px;height:72px}
.story-card{left:552px;top:1208px;width:608px;height:432px;background:#fff;box-shadow:0 6px 24px rgba(0,0,0,.12);text-align:center}
.story-card h2{margin-top:56px;font-family:"Poppins",sans-serif;font-weight:700;font-size:36px;line-height:44px}
.story-card .rule{width:60px;height:3px;background:var(--red);margin:12px auto 22px}
.story-card p{width:420px;margin:0 auto;font-size:14px;line-height:22px;color:var(--muted)}
.story-btn{margin-top:32px;width:166px;height:50px;line-height:50px}

/* section headings */
.section-title{left:0;width:1200px;text-align:center;font-family:"Poppins",sans-serif;font-weight:700;font-size:40px;line-height:50px}
.section-sub{left:0;width:1200px;text-align:center;font-family:"Poppins",sans-serif;font-weight:600;font-size:13px;letter-spacing:5px;color:var(--red)}
.section-rule{left:560px;width:80px;height:3px;background:var(--red)}

/* split panels */
.split{left:112px;width:980px;background:#fff;box-shadow:0 4px 20px rgba(0,0,0,.1)}
.split-red{position:absolute;top:0;width:490px;height:100%;background:var(--red);color:#fff;font-size:15px;line-height:22px;text-align:center;padding:40px 46px}
.split-art{position:absolute}
.card-box{left:620px;top:70px;width:250px;height:170px;border-radius:12px;transform:rotate(-14deg);
  background:linear-gradient(90deg,#ffffff 0%,#f1f1f1 45%,#d93a41 46%,#b5121b 100%);box-shadow:-8px 12px 22px rgba(0,0,0,.18)}
.gift-box{left:60px;top:60px;width:330px;height:250px;border-radius:6px;transform:rotate(-4deg);
  background:radial-gradient(circle at 50% 45%,#d23a42 0%,#a3121a 45%,#6f0910 100%);box-shadow:0 14px 28px rgba(0,0,0,.25)}
.gift-deck{left:120px;top:250px;width:230px;height:110px;border-radius:6px;transform:rotate(-4deg);
  background:linear-gradient(180deg,#ffffff,#e7e7e7);box-shadow:0 6px 16px rgba(0,0,0,.2)}

/* hand of cards sketch */
.deck-sketch{left:404px;top:2856px;width:392px;height:200px;border-radius:12px;
  background:linear-gradient(180deg,#ffffff 0%,#f3f3f3 60%,#e4e4e4 100%);border:2px solid #2a2a2a}

/* footer */
.site-footer{left:0;top:3100px;width:1200px;height:280px;background:var(--footer)}
.foot-col{top:3124px;font-size:13px;color:var(--muted);line-height:28px}
.foot-col h4{font-family:"Poppins",sans-serif;font-weight:700;font-size:17px;color:var(--ink);margin-bottom:12px;letter-spacing:.3px;line-height:26px}
.foot-col .row{display:flex;gap:10px;align-items:flex-start}
.email-input{width:208px;height:36px;background:#fff;border:1px solid #ddd;margin-top:4px}
.signup{margin-top:12px;width:96px;height:36px;line-height:36px;border-radius:3px;font-size:12px}
.socials{display:flex;gap:12px;margin-top:4px}
.socials span{width:34px;height:34px;border-radius:50%;background:var(--ink)}
.bottom-bar{left:0;top:3380px;width:1200px;height:64px;background:var(--red);color:#fff;font-size:14px;text-align:center;line-height:64px}
</style>
</head>
<body>

<header class="site-header abs">
  <div class="logo abs">Lumbra</div>
  <nav class="nav abs">
    <a class="active" href="#">Home</a>
    <a href="#">About us</a>
    <a href="#">Shop</a>
    <a href="#">Contact us</a>
    <span class="region">Eswatini ▾ <span class="region-dot" role="img" aria-label="Eswatini flag colours"></span></span>
  </nav>
</header>

<section class="hero abs"></section>
<h1 class="hero-title abs">LUMBRA</h1>
<p class="hero-text abs">Lorem ipsum dolor sit amet, consectetur adipiscing elit, sed do eiusmod tempor incididunt ut labore magna aliqua.</p>
<a class="btn hero-btn abs" href="#">SHOP NOW</a>
<div class="hero-fan abs" role="img" aria-label="Fanned aces and kings behind the deck"></div>
<div class="hero-card card-back abs" role="img" aria-label="Card back in blue, yellow and red stripes"></div>

<div class="band abs">PLAYING CARDS</div>

<svg class="arrow abs" style="left:36px" width="24" height="32" viewBox="0 0 24 32"><path d="M22 0 L0 16 L22 32Z" fill="#9a9a9a"/></svg>
<article class="product abs" style="left:112px"><div class="product-fan" role="img" aria-label="Fanned aces"></div><div class="product-card card-back" role="img" aria-label="Striped card back"></div><h3 class="product-name">Lorem ipsum dolor</h3><div class="product-rule"></div></article>
<article class="product abs" style="left:448px"><div class="product-fan" role="img" aria-label="Fanned aces"></div><div class="product-card card-back" role="img" aria-label="Striped card back"></div><h3 class="product-name">Lorem ipsum dolor</h3><div class="product-rule"></div></article>
<article class="product abs" style="left:784px"><div class="product-fan" role="img" aria-label="Fanned aces"></div><div class="product-card card-back" role="img" aria-label="Striped card back"></div><h3 class="product-name">Lorem ipsum dolor</h3><div class="product-rule"></div></article>
<svg class="arrow abs" style="left:1140px" width="24" height="32" viewBox="0 0 24 32"><path d="M2 0 L24 16 L2 32Z" fill="#b5121b"/></svg>

<div class="story-photo abs" role="img" aria-label="Waterfall over large rocks surrounded by forest"></div>
<svg class="play abs" viewBox="0 0 72 72"><circle cx="36" cy="36" r="36" fill="#b5121b"/><path d="M29 23 L50 36 L29 49Z" fill="#fff"/></svg>
<section class="story-card abs">
  <h2>Our Story</h2>
  <div class="rule"></div>
  <p>Lorem ipsum dolor sit amet, consectetur adipiscing elit, sed do eiusmod tempor incididunt ut labore et dolore magna aliqua. Ut enim ad minim veniam, quis nostrud exercitation ullamco laboris nisi ut aliquip ex ea commodo consequat. Duis aute irure dolor in reprehenderit in voluptate velit esse cillum dolore eu fugiat nulla pariatur. Lorem ipsum dolor sit amet, consectetur adipiscing elit.</p>
  <a class="btn story-btn" href="#">LEARN MORE ⊕</a>
</section>

<h2 class="section-title abs" style="top:1736px">Why Choose us</h2>
<div class="section-rule abs" style="top:1796px"></div>
<div class="section-sub abs" style="top:1810px">LUMBRA</div>
<section class="split abs" style="top:1852px;height:376px">
  <div class="split-red" style="left:0">Lorem ipsum dolor sit amet, consectetur adipiscing elit, sed do eiusmod tempor incididunt ut labore et dolore magna aliqua. Ut enim ad minim veniam, quis nostrud exercitation ullamco laboris nisi ut aliquip ex ea commodo consequat. Duis aute irure dolor in reprehenderit in voluptate velit esse cillum dolore eu fugiat nulla pariatur. Lorem ipsum dolor sit amet, consectetur adipiscing elit, sed do eiusmod tempor incididunt ut labore et dolore magna aliqua. Ut enim ad minim veniam, quis nostrud exercitation ullamco laboris nisi ut aliquip ex ea commodo.</div>
  <div class="split-art card-box" role="img" aria-label="Red and white card box with the deck sliding out"></div>
</section>

<h2 class="section-title abs" style="top:2262px">What we do</h2>
<div class="section-rule abs" style="top:2322px"></div>
<div class="section-sub abs" style="top:2336px">WORKING PROCESS</div>
<section class="split abs" style="top:2388px;height:432px">
  <div class="split-art gift-box" role="img" aria-label="Red patterned card box lid"></div>
  <div class="split-art gift-deck" role="img" aria-label="Deck of cards resting in the open box"></div>
  <div class="split-red" style="left:490px;padding-top:62px">Lorem ipsum dolor sit amet, consectetur adipiscing elit, sed do eiusmod tempor incididunt ut labore et dolore magna aliqua. Ut enim ad minim veniam, quis nostrud exercitation ullamco laboris nisi ut aliquip ex ea commodo consequat. Duis aute irure dolor in reprehenderit in voluptate velit esse cillum dolore eu fugiat nulla pariatur. Lorem ipsum dolor sit amet, consectetur adipiscing elit, sed do eiusmod tempor incididunt ut labore et dolore magna aliqua. Ut enim ad minim veniam, quis nostrud exercitation ullamco laboris nisi ut aliquip ex ea commodo.</div>
</section>

<div class="deck-sketch abs" role="img" aria-label="Black line sketch of a fanned hand of playing cards"></div>

<footer class="site-footer abs"></footer>
<div class="foot-col abs" style="left:112px;width:240px">
  <h4>CONTACT INFO</h4>
  <div class="row"><svg width="12" height="16" viewBox="0 0 12 16" style="margin-top:6px;flex:none"><path d="M6 0a6 6 0 0 0-6 6c0 4.5 6 10 6 10s6-5.5 6-10a6 6 0 0 0-6-6zm0 8.5A2.5 2.5 0 1 1 6 3.5a2.5 2.5 0 0 1 0 5z" fill="#555"/></svg><span style="line-height:20px;margin-top:4px">Lorem ipsum dolor sit amet, consectetur adipiscing elit</span></div>
  <div class="row"><svg width="14" height="14" viewBox="0 0 14 14" style="margin-top:7px;flex:none"><path d="M3 0l3 3-2 2c1 2 3 4 5 5l2-2 3 3-2 3C6 14 0 8 0 3z" fill="#555"/></svg>+1 555 014 2290</div>
  <div class="row"><svg width="14" height="10" viewBox="0 0 14 10" style="margin-top:9px;flex:none"><rect width="14" height="10" fill="#555"/><path d="M0 0l7 5 7-5" stroke="#fff" fill="none"/></svg>info@lumbradeck.com</div>
</div>
<div class="foot-col abs" style="left:452px">
  <h4>LINKS</h4>
  <div>About</div><div>Careers</div><div>Return Policy</div><div>Contact</div>
</div>
<div class="foot-col abs" style="left:652px">
  <h4>EMAIL SIGNUP</h4>
  <div class="email-input"></div>
  <div class="btn signup">SIGNUP</div>
</div>
<div class="foot-col abs" style="left:960px">
  <h4>FOLLOW US</h4>
  <div class="socials"><span></span><span></span><span></span></div>
</div>

<div class="bottom-bar abs">© Copyrights 2020 / All Rights Reserved</div>

</body>
</html>
```